Webshop for furniture and lamps

We need a design for a web shop with APP that should have two options:
1-Webshop in general which should attract to private customer in general and
2-Website that is meant to attract big customers as hotels and restaurants who would have their own customerize login.

That's the idea behind the shop.

It should be diveded into 4 parts
vintage furniture
rattan set outdoor and indoor
lamps and
wooden wall decor

The name of the shop is loma vereda!

Please kindly make me an offer.

Reason: Dear designers, so far there hasn't been a design that really matched. Look up German web sites like www.glimmerhof-wohnen.de or www.sitzraum77.de... Haven't been convinced by designs! Sorry folks. Please submit some new ones. Kind regards Ned

```html
<!DOCTYPE html>
<html lang="en">
<head>
<meta charset="utf-8">
<title>Loma Vereda – Furniture &amp; Lamps</title>
<link href="https://fonts.googleapis.com/css2?family=Oswald:wght@400;500;700&family=Open+Sans:wght@400;600;700&display=swap" rel="stylesheet">
<style>
:root{
  --orange:#f28a1a;
  --orange-dark:#d9730c;
  --ink:#222;
  --text:#555;
  --muted:#888;
  --dark:#2b2b2b;
  --darker:#1c1c1c;
  --wood:#3a2e26;
  --wood-deep:#2f251f;
  --line:#d6d6d6;
  --panel:#f1f1f1;
  --white:#fff;
}
*{box-sizing:border-box;margin:0;padding:0}
html,body{width:1200px;height:3248px;overflow:hidden;background:var(--white)}
body{font-family:"Open Sans",Arial,sans-serif;color:var(--text);font-size:14px;position:relative}
.h{font-family:"Oswald","Arial Narrow",sans-serif;text-transform:uppercase;color:var(--ink)}
section,header,footer,.band{position:absolute;left:0;width:1200px}

/* top bar */
.topbar{top:0;height:32px;background:var(--darker);color:#bbb;font-size:12px;display:flex;align-items:center;justify-content:space-between;padding:0 100px}
.topbar ul{display:flex;gap:26px;list-style:none;align-items:center}
.topbar li.checkout{background:var(--orange);color:#fff;padding:8px 14px}

/* header */
.site-header{top:32px;height:128px;display:flex;align-items:center;justify-content:space-between;padding:0 100px;border-bottom:1px solid #eee}
.brand{display:flex;align-items:center;gap:14px}
.brand-mark{width:34px;height:34px;background:var(--orange)}
.brand-name{font-family:"Oswald",sans-serif;font-weight:700;font-size:34px;color:var(--ink);text-transform:uppercase;letter-spacing:.5px}
.main-nav{display:flex;gap:30px;list-style:none;align-items:center}
.main-nav li{font-family:"Oswald",sans-serif;font-size:15px;font-weight:500;color:var(--ink);text-transform:uppercase}

/* hero */
.hero{top:160px;height:448px;background:linear-gradient(100deg,#e9e3da 0%,#c9b9a3 25%,#8a6a4c 45%,#b59a78 65%,#e6ddd0 100%)}
.hero-label{position:absolute;right:120px;top:92px;text-align:center}
.hero-label .small{background:var(--orange);color:#fff;font-family:"Oswald",sans-serif;font-size:22px;padding:6px 28px;display:inline-block;text-transform:uppercase;font-weight:500}
.hero-label .big{background:var(--orange-dark);color:#fff;font-family:"Oswald",sans-serif;font-size:50px;font-weight:700;padding:4px 26px;text-transform:uppercase;margin-top:6px}
.hero-label .sub{background:var(--orange);color:#fff;font-family:"Oswald",sans-serif;font-size:30px;font-weight:500;padding:2px 24px;display:inline-block;text-transform:uppercase;margin-top:6px}

/* section title */
.title-box{position:absolute;left:50%;transform:translateX(-50%);border:2px solid var(--ink);padding:10px 30px;font-family:"Oswald",sans-serif;font-size:20px;font-weight:500;text-transform:uppercase;color:var(--ink);white-space:nowrap;background:#fff}
.title-box.light{border-color:#fff;color:#fff;background:transparent}
.title-rule{position:absolute;left:100px;width:1000px;height:1px;background:var(--line)}

/* shop */
.shop{top:608px;height:932px}
.cat-nav{position:absolute;top:166px;width:100%;text-align:center;font-size:12px;text-transform:uppercase;color:var(--muted);letter-spacing:.5px}
.cat-nav .on{color:var(--orange);font-weight:700}
.intro{position:absolute;top:192px;width:100%;text-align:center;font-size:12px}
.read-link{position:absolute;top:238px;width:100%;text-align:center;font-size:11px;font-weight:700;color:var(--ink);text-transform:uppercase}
.products{position:absolute;top:320px;left:140px;width:920px;display:flex;justify-content:space-between}
.product{width:250px;text-align:center}
.product .pic{height:230px;margin-bottom:50px}
.pic.p1{background:linear-gradient(160deg,#6f8aa6,#b04236 50%,#d4a24a)}
.pic.p2{background:linear-gradient(160deg,#c7b28f,#8f7457 60%,#6e5540)}
.pic.p3{background:linear-gradient(160deg,#7a5332,#4e321e)}
.product .name{font-family:"Oswald",sans-serif;font-size:16px;font-weight:500;color:var(--ink);text-transform:uppercase}
.product .price{font-family:"Oswald",sans-serif;font-size:18px;color:var(--orange);margin:14px 0 10px}
.product p{font-size:12px;line-height:1.5}
.shop-now{position:absolute;top:780px;left:50%;transform:translateX(-50%);width:240px;height:52px;background:var(--orange);color:#fff;font-family:"Oswald",sans-serif;font-size:22px;font-weight:700;display:flex;align-items:center;justify-content:center;text-transform:uppercase;clip-path:polygon(0 0,100% 0,92% 100%,8% 100%)}

/* blog */
.blog{top:1540px;height:640px;background:linear-gradient(180deg,var(--wood) 0%,var(--wood-deep) 100%)}
.blog .title-box{top:80px}
.posts{position:absolute;top:208px;left:100px;width:1000px;display:grid;grid-template-columns:repeat(3,1fr);column-gap:56px;row-gap:56px}
.post .head{display:flex;align-items:center;gap:14px;margin-bottom:14px}
.post .num{width:40px;height:40px;background:var(--orange);color:#fff;font-family:"Oswald",sans-serif;font-size:22px;font-weight:700;display:flex;align-items:center;justify-content:center}
.post .head span{font-family:"Oswald",sans-serif;font-size:17px;color:#fff;text-transform:uppercase;font-weight:500}
.post p{color:#cfc6bd;font-size:12px;line-height:1.55;margin-bottom:14px}
.btn-outline{display:inline-block;border:1px solid #cfc6bd;color:#fff;font-size:11px;font-weight:700;padding:6px 14px;text-transform:uppercase}

/* outdoor banner */
.outdoor{top:2180px;height:220px;display:flex}
.outdoor .pic{width:540px;background:linear-gradient(120deg,#d9cdb8,#a88e66 55%,#6f5a3d)}
.outdoor .promo{flex:1;background:var(--orange);display:flex;align-items:center;justify-content:space-between;padding:0 70px 0 60px}
.promo .big{font-family:"Oswald",sans-serif;font-size:40px;font-weight:700;color:#fff;text-transform:uppercase;line-height:1}
.promo .small{font-family:"Oswald",sans-serif;font-size:18px;color:#fff;text-transform:uppercase;margin-top:6px}
.btn-dark{background:var(--dark);color:#fff;font-family:"Oswald",sans-serif;font-size:16px;padding:12px 22px;text-transform:uppercase}

/* video */
.video{top:2400px;height:512px}
.video .title-box{top:104px}
.arrows{position:absolute;top:120px;left:1010px;display:flex;gap:6px}
.arrows div{width:36px;height:36px;background:var(--orange);display:flex;align-items:center;justify-content:center}
.video-card{position:absolute;top:220px;left:100px;width:890px;height:240px;background:var(--panel);display:flex}
.video-card .pic{width:280px;background:linear-gradient(140deg,#a89c8a,#6c5a45 60%,#3f3226);position:relative}
.play{position:absolute;left:50%;top:50%;width:56px;height:56px;margin:-28px 0 0 -28px;border-radius:50%;background:#fff;display:flex;align-items:center;justify-content:center}
.video-card .txt{padding:24px 30px;flex:1}
.video-card h3{font-size:20px;font-weight:500;margin-bottom:14px}
.video-card p{font-size:12px;line-height:1.6;margin-bottom:16px}
.btn-line{display:inline-block;border:1px solid var(--ink);color:var(--ink);font-size:11px;font-weight:700;padding:6px 14px;text-transform:uppercase}

/* services */
.services{top:2912px;height:268px;background:var(--dark);display:flex;padding:0 100px}
.services::before{content:"";position:absolute;left:0;top:0;width:100%;height:88px;background:var(--orange)}
.service{flex:1;position:relative;text-align:center;border-left:1px solid #444}
.service:first-child{border-left:none}
.service .bar{height:88px;display:flex;align-items:center;justify-content:center;gap:16px}
.service .bar span{font-family:"Oswald",sans-serif;font-size:22px;font-weight:700;color:#fff;text-transform:uppercase}
.service p{color:#bbb;font-size:12px;line-height:1.55;padding:22px 40px 14px}
.cards{display:flex;justify-content:center;gap:8px;margin-bottom:14px}
.cards i{width:40px;height:24px;background:#e8e8e8;display:block}

/* bottom bar */
.site-footer{top:3180px;height:68px;background:var(--darker);display:flex;align-items:center;justify-content:space-between;padding:0 100px;font-size:12px;color:#aaa;text-transform:uppercase}
.site-footer ul{display:flex;list-style:none;gap:30px}
.social{display:flex;gap:8px}
.social i{width:24px;height:24px;border-radius:50%;background:#777;display:block}
</style>
</head>
<body>

<div class="band topbar">
  <span>Dear Ned, welcome to our online store</span>
  <ul><li>Login</li><li>My Account ▾</li><li>0 item</li><li class="checkout">Checkout</li></ul>
</div>

<header class="site-header">
  <div class="brand"><div class="brand-mark"></div><div class="brand-name">Loma Vereda</div></div>
  <ul class="main-nav">
    <li>Home</li><li>Shop by Brand</li><li>Top Sellers</li><li>Clearance</li><li>Help Center</li><li>My Favorites</li>
    <li><svg width="16" height="16" viewBox="0 0 16 16"><circle cx="6.5" cy="6.5" r="5" fill="none" stroke="#222" stroke-width="2"/><line x1="10.5" y1="10.5" x2="15" y2="15" stroke="#222" stroke-width="2"/></svg></li>
  </ul>
</header>

<section class="hero" role="img" aria-label="Bedroom interior with bed, lamp and wooden wall decor">
  <div class="hero-label">
    <div class="small">Lorem ipsum dolor</div>
    <div class="big">Accusantium</div>
    <div class="sub">Unde</div>
  </div>
</section>

<section class="shop">
  <div class="title-rule" style="top:97px"></div>
  <div class="title-box" style="top:76px">Shop by Category</div>
  <div class="cat-nav">Vintage Furniture &nbsp;|&nbsp; <span class="on">Rattan Set Outdoor and Indoor</span> &nbsp;|&nbsp; Lamps &nbsp;|&nbsp; Wooden Wall Decor</div>
  <div class="intro">Sed perspiciatis unde omnis iste natus error sit voluptatem accusantium doloremque laudantium, totam rem aperiam eaque ipsa quae ab illo.</div>
  <div class="read-link">Read more</div>
  <div class="products">
    <div class="product"><div class="pic p1" role="img" aria-label="Painted vintage chest of drawers"></div><div class="name">Voluptatem fugit aut</div><div class="price">$479.00</div><p>Lorem ipsum dolor sit amet <b>voluptatem</b> fugit aut odit aut fugit, sed quia consequuntur magni dolores.</p></div>
    <div class="product"><div class="pic p2" role="img" aria-label="Weathered wooden trunk"></div><div class="name">Voluptatem fugit aut</div><div class="price">$479.00</div><p>Lorem ipsum dolor sit amet voluptatem fugit aut odit aut fugit, sed quia consequuntur magni dolores.</p></div>
    <div class="product"><div class="pic p3" role="img" aria-label="Dark wooden cabinet with open door"></div><div class="name">Voluptatem fugit aut</div><div class="price">$479.00</div><p>Lorem ipsum <b>dolor</b> sit amet voluptatem fugit aut odit aut fugit, sed quia consequuntur magni dolores.</p></div>
  </div>
  <div class="shop-now">Shop Now</div>
</section>

<section class="blog" role="img" aria-label="Dark wood background behind the latest blog news">
  <div class="title-box light">Lates News from Blog</div>
  <div class="posts">
    <div class="post"><div class="head"><div class="num">1</div><span>Amet voluptatem</span></div><p>Lorem ipsum dolor sit amet nemo enim ipsam voluptatem quia voluptas sit aspernatur aut odit aut fugit, sed quia consequuntur.</p><span class="btn-outline">Read more</span></div>
    <div class="post"><div class="head"><div class="num">2</div><span>Amet voluptatem</span></div><p>Lorem ipsum dolor sit amet nemo enim ipsam voluptatem quia voluptas sit aspernatur aut odit aut fugit, sed quia consequuntur.</p><span class="btn-outline">Read more</span></div>
    <div class="post"><div class="head"><div class="num">3</div><span>Amet voluptatem</span></div><p>Lorem ipsum dolor sit amet nemo enim ipsam voluptatem quia voluptas sit aspernatur aut odit aut fugit, sed quia consequuntur.</p><span class="btn-outline">Read more</span></div>
    <div class="post"><div class="head"><div class="num">4</div><span>Amet voluptatem</span></div><p>Lorem ipsum dolor sit amet nemo enim ipsam voluptatem quia voluptas sit aspernatur aut odit aut fugit, sed quia consequuntur.</p><span class="btn-outline">Read more</span></div>
    <div class="post"><div class="head"><div class="num">5</div><span>Amet voluptatem</span></div><p>Lorem ipsum dolor sit amet nemo enim ipsam voluptatem quia voluptas sit aspernatur aut odit aut fugit, sed quia consequuntur.</p><span class="btn-outline">Read more</span></div>
    <div class="post"><div class="head"><div class="num">6</div><span>Amet voluptatem</span></div><p>Lorem ipsum dolor sit amet nemo enim ipsam voluptatem quia voluptas sit aspernatur aut odit aut fugit, sed quia consequuntur.</p><span class="btn-outline">Read more</span></div>
  </div>
</section>

<section class="outdoor">
  <div class="pic" role="img" aria-label="Outdoor rattan lounge furniture on a terrace"></div>
  <div class="promo">
    <div><div class="big">Outside Furniture</div><div class="small">Big savings on quality items</div></div>
    <div class="btn-dark">Shop Now</div>
  </div>
</section>

<section class="video">
  <div class="title-rule" style="top:125px"></div>
  <div class="title-box">Watch Our Video</div>
  <div class="arrows">
    <div><svg width="12" height="14" viewBox="0 0 12 14"><path d="M9 1 3 7l6 6" fill="none" stroke="#fff" stroke-width="2.5"/></svg></div>
    <div><svg width="12" height="14" viewBox="0 0 12 14"><path d="M3 1l6 6-6 6" fill="none" stroke="#fff" stroke-width="2.5"/></svg></div>
  </div>
  <div class="video-card">
    <div class="pic" role="img" aria-label="Video still of a vintage wooden sideboard in a room">
      <div class="play"><svg width="18" height="20" viewBox="0 0 18 20"><path d="M2 1l15 9-15 9z" fill="#222"/></svg></div>
    </div>
    <div class="txt">
      <h3 class="h">Sed enim accusantium</h3>
      <p>Lorem ipsum dolor sit amet nemo enim ipsam voluptatem quia voluptas sit aspernatur aut odit aut fugit, sed quia consequuntur magni dolores eos qui ratione voluptatem sequi nesciunt neque porro quisquam est qui dolorem.</p>
      <span class="btn-line">Read more</span>
    </div>
  </div>
</section>

<section class="services">
  <div class="service">
    <div class="bar"><svg width="30" height="26" viewBox="0 0 30 26"><rect x="1" y="4" width="28" height="20" rx="2" fill="none" stroke="#fff" stroke-width="2.5"/><rect x="1" y="9" width="28" height="4" fill="#fff"/></svg><span>Payment Method</span></div>
    <p>Lorem ipsum dolor sit amet nemo enim ipsam voluptatem quia voluptas sit aspernatur aut odit aut fugit sed quia.</p>
    <div class="cards"><i></i><i></i><i></i><i></i></div>
    <span class="btn-outline">Read more</span>
  </div>
  <div class="service">
    <div class="bar"><svg width="36" height="26" viewBox="0 0 36 26"><rect x="1" y="3" width="21" height="16" fill="#fff"/><path d="M22 8h7l6 6v5H22z" fill="#fff"/><circle cx="8" cy="21" r="4" fill="#fff" stroke="#f28a1a" stroke-width="2"/><circle cx="28" cy="21" r="4" fill="#fff" stroke="#f28a1a" stroke-width="2"/></svg><span>Free Shipping</span></div>
    <p>Lorem ipsum dolor sit amet nemo enim ipsam voluptatem quia voluptas sit aspernatur aut odit aut fugit sed quia consequuntur magni.</p>
    <span class="btn-outline">Read more</span>
  </div>
  <div class="service">
    <div class="bar"><svg width="24" height="28" viewBox="0 0 24 28"><path d="M6 12V8a6 6 0 0 1 12 0v4" fill="none" stroke="#fff" stroke-width="3"/><rect x="2" y="12" width="20" height="15" rx="2" fill="#fff"/></svg><span>Secure Shopping</span></div>
    <p>Lorem ipsum dolor sit amet nemo enim ipsam voluptatem quia voluptas sit aspernatur aut odit aut fugit sed quia consequuntur magni.</p>
    <span class="btn-outline">Read more</span>
  </div>
</section>

<footer class="site-footer">
  <span>© 2014 Loma Vereda. All rights reserved.</span>
  <ul><li>About us</li><li>Terms and use</li><li>Privacy policy</li><li>FAQs</li><li>Contact us</li></ul>
  <div class="social"><i></i><i></i><i></i><i></i><i></i><i></i></div>
</footer>

</body>
</html>
```